Doctor to Patient Management Website

I need a design for a health management website that connects doctors to patients. The website will consist of: A main page mainly describing our goal, services, and initiatives towards (Who we are AKA "About Us", Our services, Contact Us, Quick Links for health tips, Language selection, Find a doctor, search bar, Member Login Section, small glossary section below with links to all entities mentioned prior, Help section (Helpful tips and tutorials, Used to request help from admin, customer service, to resolve issues or get assistance). A profile page with two types:1) Doctor Profile: Doctor Personal info (First, Last, Middle Name, Title), Clinic, Hospital Info, Department, Credentials, Years of Experience, Patients rating, #Patients seen during the current week, #Patients seen in total, Picture, Link to email doctor, Link to print doctor's profile). Tabs for "About Me", "Contact Info", "Ratings & Comments", "Documents" (To be downloaded and uploaded by patient), "Patients (List of Patients alphabetical order by name)", "Calendar" (to see doctor's availability for booking) underneath all links. 2) Patient profile: About me, Personal Info, Height, Weight, Blood Type, Age, DOB, Name, etc..., Message and email link.Picture of patient with menu made of "Personal Data", "Biometrics", "Allergies", "Illnesses", "Medications", "Medical Procedures", "Doctors" treating the patient, "Documents" (To be downloaded and uploaded by patient). Underneath all, other patients he or she is related to (For example: family member, so patient can't connect to other patients who are family members)3) Login section: New Users will have option to register using:First Name (Required), Last Name, Middle (not required), Address (Not required), City (Required), Country (Required), Email (Not required), Phone Number (Required), Choose UserName, Password, Account Type (Doctor or Patient). Once registered, they will log in using UserName, Password, and Account_Type.Curent Users will log in using UserName, Password, and Account_Type and option to retrieve username or password.Pages to include (Login Page - Registration Page - Retrieve Username and Reset Password Page)Please see link below:https://plumcrate-adwerks.net/importance-claiming-vantorix-quibble-zarn/Pictures are attached to this project as an inspirationFYI: Dummy text can be used to fill in the business, services, and descriptive information. Feel free to include your own ideas in the layout, design, categories, patterns, and more to and showcase your talent. Design and pictures provided are available as source of ideas.

Target Market(s)

Age: 21+ / Family Oriented / Medical Sector / Metropolitan Area / Educated and non Educated Users

Industry/Entity Type

Health Care

Number of Pages Required

5+ page

Font styles to use
Sans Serif

Colors

Designer to choose colors to be used in the design.

Requirements
Must have
• Thin layer design
• Simple font - No serif
• Clean menu with light but solid colors (No Gradient effect)
Nice to have
• Different color themes (2 or 3) can be combined
• Sample pictures for illustration (either as an ad or to go with the flow of your design)
• Dashboard Feel (Suggested but not required)
Should not have
• Artistic fonts - with Serif
• Dark color themes

```html
<!DOCTYPE html>
<html lang="en">
<head>
<meta charset="utf-8">
<title>Mediora — Doctor to Patient Care</title>
<link href="https://fonts.googleapis.com/css2?family=Montserrat:wght@400;500;600;700&family=Open+Sans:wght@400;600&display=swap" rel="stylesheet">
<style>
:root{
  --blue:#2a8fdc;
  --blue-dark:#1f72bd;
  --ink:#222;
  --text:#555;
  --grey:#e9e9e9;
  --faint:rgba(42,143,220,.10);
  --footer:#1d1d1d;
  --white:#fff;
}
*{box-sizing:border-box;margin:0;padding:0}
html,body{width:1200px;height:4918px;overflow:hidden}
body{position:relative;background:var(--white);font-family:"Open Sans",Arial,sans-serif;color:var(--text)}
.abs{position:absolute}
h1,h2,h3,.btn,.nav a,.logo{font-family:"Montserrat",Arial,sans-serif}

/* top bar */
.topbar{left:0;top:0;width:1200px;height:38px;background:var(--blue);color:#fff;font-size:13px}
.topbar span{position:absolute;top:11px}
/* header */
.header{left:0;top:38px;width:1200px;height:118px;background:#fff}
.logo{font-weight:700;color:var(--blue);font-size:30px;letter-spacing:1px}
.call{left:112px;top:36px;display:flex;gap:12px;align-items:center}
.call small{display:block;color:var(--blue);font-size:13px;font-weight:600}
.call b{font-size:13px;color:#333}
.search{left:786px;top:32px;width:296px;height:50px;border:1px solid #ddd;border-radius:25px;padding:0 0 0 22px;line-height:48px;font-size:14px;color:#999}
.search i{position:absolute;right:4px;top:4px;width:40px;height:40px;border-radius:50%;background:var(--blue)}
.nav{left:0;top:156px;width:1200px;height:64px;border-top:1px solid #e5e5e5;border-bottom:1px solid #e5e5e5;background:#fff}
.nav a{position:absolute;top:22px;font-size:15px;color:#333;text-decoration:none;font-weight:500}
.login{right:90px;top:0;width:260px;height:64px;background:var(--blue);color:#fff;font-weight:600;font-size:15px;text-align:center;line-height:64px}

/* hero */
.hero{left:0;top:220px;width:1200px;height:640px;background:linear-gradient(100deg,#d7dfe7 0%,#eef2f5 40%,#f6f7f9 70%,#e6eaee 100%)}
.hero h1{left:560px;top:130px;width:600px;color:var(--blue);font-size:44px;font-weight:700;line-height:1.15}
.hero h2{left:560px;top:250px;font-size:36px;color:#111;font-weight:700}
.btn{display:inline-block;background:var(--blue);color:#fff;border-radius:40px;font-weight:600;text-transform:uppercase}
.hero .btn{left:562px;top:320px;height:64px;padding:0 34px 0 80px;line-height:64px;font-size:20px}
.btn .ic{position:absolute;left:6px;top:6px;width:52px;height:52px;border-radius:50%;background:#fff}

.section-title{text-align:center;width:1200px;left:0;color:var(--blue);font-size:32px;font-weight:700}
.ghost{text-align:center;width:1200px;left:0;color:var(--faint);font-size:62px;font-weight:700;font-family:"Montserrat",Arial,sans-serif;white-space:nowrap}
p.body{font-size:15px;line-height:1.95}

.photo{background:linear-gradient(135deg,#c9d6e1,#eef1f4);}
.circle-photo{border-radius:50%;overflow:hidden}

.grey{left:0;width:1200px;background:var(--grey)}
.tile{position:absolute;width:310px;height:175px}
.vid{position:absolute;width:315px;height:218px;border:2px solid #fff;outline:1px solid #999;outline-offset:4px}
.vid .play{position:absolute;left:50%;top:50%;width:44px;height:44px;margin:-22px 0 0 -22px;border-radius:50%;background:#fff}
.vid .play:after{content:"";position:absolute;left:17px;top:13px;border-left:14px solid #333;border-top:9px solid transparent;border-bottom:9px solid transparent}

.contact-item{width:300px;text-align:center;font-size:16px;color:#333;line-height:1.7}
.contact-item .ring{width:86px;height:86px;border-radius:50%;background:var(--blue);margin:0 auto 18px;display:flex;align-items:center;justify-content:center}

.field{position:absolute;height:48px;border-bottom:1px solid #ddd;font-size:13px;color:#888;padding-top:14px;padding-left:16px;width:430px}
.field.msg{height:192px;border:1px solid #ddd}

.footer{left:0;top:4500px;width:1200px;height:418px;background:var(--footer);color:#ddd}
.footer h3{font-size:17px;color:#fff;font-weight:700}
.footer ul{list-style:none;font-size:13px;line-height:25px}
.footer li:before{content:"•";margin-right:10px}
.social{width:30px;height:30px;border-radius:50%;border:1px solid #ddd;display:inline-block;margin-right:8px}
.checklist{list-style:none;font-size:15px;line-height:34px;color:#444}
.checklist li{display:flex;align-items:center;gap:10px}
.tick{width:16px;height:16px;border-radius:50%;background:#222;position:relative}
.tick:after{content:"";position:absolute;left:5px;top:3px;width:4px;height:7px;border:solid #fff;border-width:0 2px 2px 0;transform:rotate(45deg)}
</style>
</head>
<body>

<!-- top bar -->
<div class="abs topbar">
  <span style="left:112px">✉ info@mediora-care.com</span>
  <span style="left:700px">EN ▾</span>
  <span style="left:786px">⌖ 4120 Linden Ave, Fairview, VA 22010</span>
</div>

<!-- header -->
<div class="abs header">
  <div class="abs call">
    <svg width="36" height="36" viewBox="0 0 24 24"><path fill="#2a8fdc" d="M6.6 10.8c1.4 2.8 3.8 5.1 6.6 6.6l2.2-2.2c.3-.3.7-.4 1-.2 1.1.4 2.3.6 3.6.6.6 0 1 .4 1 1V20c0 .6-.4 1-1 1C10.6 21 3 13.4 3 4c0-.6.4-1 1-1h3.5c.6 0 1 .4 1 1 0 1.3.2 2.5.6 3.6.1.3 0 .7-.2 1z"/></svg>
    <div><small>Call us:</small><b>(555) 014-2277</b></div>
  </div>
  <div class="abs logo" style="left:520px;top:38px">MEDIORA</div>
  <div class="abs search">Search<i><svg width="40" height="40" viewBox="0 0 40 40"><circle cx="18" cy="18" r="6" fill="none" stroke="#fff" stroke-width="2.5"/><path d="M22.5 22.5l5 5" stroke="#fff" stroke-width="2.5"/></svg></i></div>
</div>

<!-- nav -->
<div class="abs nav">
  <a style="left:128px" href="#">Home</a>
  <a style="left:222px" href="#">About Us</a>
  <a style="left:342px" href="#">Our Services</a>
  <a style="left:488px" href="#">Health Tips</a>
  <a style="left:622px" href="#">Help</a>
  <a style="left:700px" href="#">Contact Us</a>
  <div class="abs login">👤 MEMBER LOGIN</div>
</div>

<!-- hero -->
<section class="abs hero">
  <div class="abs" role="img" aria-label="Photo of a smiling male doctor and female nurse in a bright hospital corridor" style="left:40px;top:20px;width:460px;height:600px;background:linear-gradient(180deg,#cfd9e3,#9db7cf 60%,#7fa3c4)"></div>
  <h1 class="abs">We Provide Best Medical Service.</h1>
  <h2 class="abs">Best Health Care Solution.</h2>
  <div class="abs btn"><span class="ic"><svg width="52" height="52" viewBox="0 0 52 52"><circle cx="24" cy="24" r="8" fill="none" stroke="#2a8fdc" stroke-width="3"/><path d="M30 30l7 7" stroke="#2a8fdc" stroke-width="3"/></svg></span>Find a Doctor</div>
</section>
<svg class="abs" style="left:0;top:800px" width="1200" height="100" viewBox="0 0 1200 100" preserveAspectRatio="none">
  <path d="M0 55 C300 95 700 95 1200 20 L1200 100 L0 100Z" fill="#fff"/>
  <path d="M0 55 C300 90 700 85 1200 20 L1200 34 C700 100 300 102 0 68Z" fill="#2a8fdc"/>
</svg>

<!-- about -->
<section>
  <svg class="abs" style="left:92px;top:960px" width="440" height="430" viewBox="0 0 440 430">
    <path d="M30 180 A195 195 0 0 1 370 90" fill="none" stroke="#2a8fdc" stroke-width="12"/>
  </svg>
  <div class="abs circle-photo" role="img" aria-label="Illustration of a hand touching floating medical icons" style="left:108px;top:978px;width:400px;height:400px;background:radial-gradient(circle,#d9ecf8,#a9cde8);border:6px solid #fff;box-shadow:0 0 0 2px #dfe8ef"></div>
  <div class="abs ghost" style="left:560px;top:1000px;width:auto;text-align:left">WHO WE ARE AKA</div>
  <h2 class="abs" style="left:562px;top:1028px;color:var(--blue);font-size:32px;font-weight:700">WHO WE ARE AKA</h2>
  <p class="abs body" style="left:562px;top:1078px;width:540px">Sed ut perspiciatis unde omnis iste natus error sit voluptatem accusantium doloremque laudantium, totam rem aperiam, eaque ipsa quae ab illo inventore veritatis et quasi architecto beatae vitae dicta sunt explicabo. Nemo enim ipsam voluptatem quia voluptas sit aspernatur aut odit aut fugit, sed quia consequuntur magni dolores eos qui ratione voluptatem sequi nesciunt.</p>
  <div class="abs btn" style="left:562px;top:1282px;height:52px;line-height:52px;padding:0 28px 0 60px;font-size:15px"><span class="ic" style="width:42px;height:42px;left:5px;top:5px"></span>Read More</div>
</section>

<!-- services -->
<section class="abs grey" style="top:1480px;height:800px"></section>
<svg class="abs" style="left:0;top:1470px" width="1200" height="120" viewBox="0 0 1200 120" preserveAspectRatio="none">
  <path d="M0 0 H1200 V30 C800 80 400 110 0 30Z" fill="#fff"/>
  <path d="M700 70 C900 30 1100 20 1200 28 L1200 46 C1050 34 880 50 700 70Z" fill="#2a8fdc"/>
</svg>
<div class="abs ghost" style="top:1620px">OUR SERVICES</div>
<h2 class="abs section-title" style="top:1645px">OUR SERVICES</h2>
<p class="abs body" style="left:150px;top:1692px;width:900px;text-align:center;font-size:14px;line-height:1.9">Sed ut perspiciatis unde omnis iste natus error sit voluptatem accusantium doloremque laudantium, totam rem aperiam, eaque ipsa quae ab illo inventore veritatis et quasi architecto beatae vitae dicta sunt explicabo.</p>
<div class="tile photo" role="img" aria-label="Photo of a doctor consulting a patient" style="left:110px;top:1776px;background:linear-gradient(135deg,#d8cdbf,#a8b8c6)"></div>
<div class="tile" style="left:448px;top:1776px;background:var(--blue);color:#fff;padding:22px 18px">
  <div style="font-family:Montserrat,sans-serif;font-weight:700;font-size:19px">OUTDOOR CHECKUP</div>
  <div style="font-size:15px;line-height:1.6;margin-top:8px">Lorem ipsum dolor sit amet, consectetur adipiscing elit, sed</div>
  <div style="font-family:Montserrat,sans-serif;font-weight:700;font-size:13px;margin-top:12px">READ MORE »</div>
</div>
<div class="tile photo" role="img" aria-label="Photo of a pharmacy interior" style="left:780px;top:1776px;background:linear-gradient(135deg,#7fa6c8,#d6dde4)"></div>
<div class="tile photo" role="img" aria-label="Photo of a doctor with a tablet" style="left:110px;top:1970px;background:linear-gradient(135deg,#e6e9ec,#c6d1da)"></div>
<div class="tile photo" role="img" aria-label="Photo of a woman holding medication" style="left:448px;top:1970px;background:linear-gradient(135deg,#b7cde0,#e7c8c1)"></div>
<div class="tile photo" role="img" aria-label="Photo of a physiotherapy session" style="left:780px;top:1970px;background:linear-gradient(135deg,#d5dfe8,#5e88b5)"></div>
<svg class="abs" style="left:0;top:2220px" width="1200" height="120" viewBox="0 0 1200 120" preserveAspectRatio="none">
  <path d="M0 10 C400 60 800 90 1200 40 V120 H0Z" fill="#fff"/>
  <path d="M0 40 C150 30 300 20 500 30 C300 28 150 40 0 56Z" fill="#2a8fdc"/>
</svg>

<!-- health tips -->
<section>
  <div class="abs ghost" style="left:95px;top:2420px;width:auto;text-align:left">HEALTH TIPS</div>
  <h2 class="abs" style="left:95px;top:2446px;color:var(--blue);font-size:32px;font-weight:700">HEALTH TIPS</h2>
  <p class="abs body" style="left:95px;top:2494px;width:540px">Sed ut perspiciatis unde omnis iste natus error sit voluptatem accusantium doloremque laudantium, totam rem aperiam, eaque ipsa quae ab illo inventore veritatis et quasi architecto beatae vitae dicta sunt explicabo.</p>
  <ul class="abs checklist" style="left:95px;top:2590px">
    <li><span class="tick"></span>Doloremque laudantium</li>
    <li><span class="tick"></span>Doloremque laudantium</li>
    <li><span class="tick"></span>Doloremque laudantium</li>
  </ul>
  <div class="abs btn" style="left:95px;top:2702px;height:52px;line-height:52px;padding:0 28px 0 60px;font-size:15px"><span class="ic" style="width:42px;height:42px;left:5px;top:5px"></span>Read More</div>
  <svg class="abs" style="left:675px;top:2380px" width="440" height="440" viewBox="0 0 440 440">
    <path d="M80 60 A205 205 0 0 1 410 200" fill="none" stroke="#2a8fdc" stroke-width="12"/>
  </svg>
  <div class="abs circle-photo" role="img" aria-label="Photo of a doctor explaining results to an older patient" style="left:692px;top:2396px;width:404px;height:404px;background:linear-gradient(135deg,#eef1f4,#c5d3df);border:6px solid #fff;box-shadow:0 0 0 2px #dfe8ef"></div>
</section>

<!-- helpful tips -->
<section class="abs grey" style="top:2860px;height:720px"></section>
<svg class="abs" style="left:0;top:2810px" width="1200" height="110" viewBox="0 0 1200 110" preserveAspectRatio="none">
  <path d="M0 0 H1200 V40 C800 100 400 100 0 60Z" fill="#fff"/>
  <path d="M800 62 C950 40 1100 30 1200 22 V40 C1080 48 940 56 800 62Z" fill="#2a8fdc"/>
</svg>
<div class="abs ghost" style="top:2912px">HELPFUL TIPS AND TUTORIALS</div>
<h2 class="abs section-title" style="top:2940px">HELPFUL TIPS AND TUTORIALS</h2>
<div class="vid" role="img" aria-label="Video still of a family reviewing paperwork" style="left:92px;top:3026px;background:linear-gradient(135deg,#b9a58f,#e3dbd0)"><span class="play"></span></div>
<div class="vid" role="img" aria-label="Video still of a doctor with an older patient" style="left:444px;top:3026px;background:linear-gradient(135deg,#e3e6ea,#b3c0cc)"><span class="play"></span></div>
<div class="vid" role="img" aria-label="Video still of a pharmacist at a counter" style="left:796px;top:3026px;background:linear-gradient(135deg,#c6d8c2,#8fb0c8)"><span class="play"></span></div>
<div class="vid" role="img" aria-label="Video still of two nurses reading a folder" style="left:92px;top:3275px;background:linear-gradient(135deg,#2f6fa8,#9fc2e0)"><span class="play"></span></div>
<div class="vid" role="img" aria-label="Video still of a doctor consulting an older woman" style="left:444px;top:3275px;background:linear-gradient(135deg,#f2f3f5,#c8d4de)"><span class="play"></span></div>
<div class="vid" role="img" aria-label="Video still of a pharmacist assisting a customer" style="left:796px;top:3275px;background:linear-gradient(135deg,#dfe5dc,#a4b9c7)"><span class="play"></span></div>
<svg class="abs" style="left:0;top:3530px" width="1200" height="110" viewBox="0 0 1200 110" preserveAspectRatio="none">
  <path d="M0 20 C400 80 800 90 1200 40 V110 H0Z" fill="#fff"/>
  <path d="M0 40 C150 38 300 40 420 50 C300 44 150 46 0 56Z" fill="#2a8fdc"/>
</svg>

<!-- contact information -->
<section>
  <div class="abs ghost" style="top:3690px">CONTACT INFORMATION</div>
  <h2 class="abs section-title" style="top:3712px">CONTACT INFORMATION</h2>
  <div class="abs" style="left:0;top:3762px;width:1200px;text-align:center;font-size:20px;color:#333;font-family:Montserrat,sans-serif;font-weight:500">Contact us for more information</div>
  <div class="abs contact-item" style="left:152px;top:3820px">
    <div class="ring"><svg width="36" height="36" viewBox="0 0 24 24"><path d="M12 2a7 7 0 0 0-7 7c0 5 7 13 7 13s7-8 7-13a7 7 0 0 0-7-7z" fill="none" stroke="#fff" stroke-width="1.6"/><circle cx="12" cy="9" r="2.5" fill="none" stroke="#fff" stroke-width="1.6"/></svg></div>
    217 Harlow Street, Kentwood,<br>Utah - 84190
  </div>
  <div class="abs contact-item" style="left:448px;top:3820px">
    <div class="ring"><svg width="38" height="38" viewBox="0 0 24 24"><path fill="#fff" d="M6.6 10.8c1.4 2.8 3.8 5.1 6.6 6.6l2.2-2.2c.3-.3.7-.4 1-.2 1.1.4 2.3.6 3.6.6.6 0 1 .4 1 1V20c0 .6-.4 1-1 1C10.6 21 3 13.4 3 4c0-.6.4-1 1-1h3.5c.6 0 1 .4 1 1 0 1.3.2 2.5.6 3.6.1.3 0 .7-.2 1z"/></svg></div>
    Phone:<br>+1 555 014 2277
  </div>
  <div class="abs contact-item" style="left:764px;top:3820px">
    <div class="ring"><svg width="38" height="38" viewBox="0 0 24 24"><rect x="3" y="5" width="18" height="14" rx="1" fill="none" stroke="#fff" stroke-width="1.6"/><path d="M3 6l9 7 9-7" fill="none" stroke="#fff" stroke-width="1.6"/></svg></div>
    Email:<br>info@mediora-care.com
  </div>
</section>

<!-- contact form -->
<section>
  <div class="abs ghost" style="top:4030px">CONTACT FORM</div>
  <h2 class="abs section-title" style="top:4050px">CONTACT FORM</h2>
  <div class="field" style="left:168px;top:4102px">👤 First Name</div>
  <div class="field" style="left:168px;top:4158px">▦ Company</div>
  <div class="field" style="left:168px;top:4214px">✉ Email Address</div>
  <div class="field" style="left:168px;top:4270px">✆ Phone Number</div>
  <div class="field" style="left:612px;top:4102px">👤 Last Name</div>
  <div class="field msg" style="left:612px;top:4158px">✎ Message :</div>
  <div class="abs" style="left:512px;top:4320px;width:176px;height:46px;background:var(--blue);color:#fff;text-align:center;line-height:46px;font-family:Montserrat,sans-serif;font-weight:600;font-size:16px">➤ Submit</div>
</section>

<!-- footer -->
<footer class="abs footer">
  <svg class="abs" style="left:0;top:-10px" width="1200" height="70" viewBox="0 0 1200 70" preserveAspectRatio="none">
    <path d="M0 0 H1200 V10 C800 70 400 60 0 20Z" fill="#fff"/>
  </svg>
  <div class="abs logo" style="left:104px;top:170px;color:#fff;font-size:32px">MEDIORA</div>
  <div class="abs" style="left:124px;top:220px"><span class="social"></span><span class="social"></span><span class="social"></span></div>

  <h3 class="abs" style="left:328px;top:100px">QUICK LINKS</h3>
  <ul class="abs" style="left:346px;top:146px">
    <li>Home</li><li>About</li><li>Services</li><li>Help</li><li>Helpful Tips</li><li>Contact</li>
  </ul>

  <h3 class="abs" style="left:555px;top:100px">SIGN UP FOR NEWSLETTER</h3>
  <p class="abs" style="left:555px;top:146px;width:290px;font-size:13px;line-height:1.7">Want to make an impact? Provide your email and we'll be in touch.</p>
  <div class="abs" style="left:555px;top:218px;width:275px;height:40px;background:#fff;color:#888;font-size:12px;padding:12px 14px">Enter email</div>
  <div class="abs" style="left:555px;top:276px;width:130px;height:36px;background:var(--blue);color:#fff;text-align:center;line-height:36px;font-family:Montserrat,sans-serif;font-weight:700;font-size:14px">SIGN UP</div>

  <h3 class="abs" style="left:935px;top:100px">GLOSSARY</h3>
  <ul class="abs" style="left:945px;top:146px">
    <li>doloremque</li><li>doloremque</li><li>doloremque</li><li>doloremque</li><li>doloremque</li><li>doloremque</li><li>doloremque</li>
  </ul>

  <div class="abs" style="left:0;top:390px;width:1200px;text-align:center;font-size:12px;color:#ccc">Copyrights © 2019 All Rights Reserved | Privacy Policy | Terms and Conditions</div>
</footer>

</body>
</html>
```